KR Appraisals website redesign

I would like to refresh my existing website of www.krappraisals-example.com with new graphics, look and feel, as well as updated structure and wording. Content and layout changes have been uploaded to this project Brief.

My existing website has a dark feel. I am now looking for a light and energetic feel. Financial Services is my industry, so the website should be reflect that. I would also like to reflect the concepts of Trust, Service and Expertise.

The website must be serious and upmarket.

Target Market(s)

Corporate board members, CFO's, treasurers and controllers
Auditors, tax advisors, private equity and venture capital asset managers, investors, tax authorities

Industry/Entity Type

Financial Service

Coding

Coded - Design and coding required

Number of Pages Required

5+ page

Font styles to use
Sans Serif
Other font styles liked:
• Designer can choose another modern font

Colors
0355a3
3277b5
85acd3
eaf1f7
f37122
f68d4d
9bcb3c
acd037
cadf82

Requirements
Must have
• Good hi resolution pictures that convey "Finance", "Trust", "Service" or "Expertise".
• An anti-bot (such as Captcha) mechanism in the contact form.
Should not have
• Must not have all content on one rolling screen.

```html
<!DOCTYPE html>
<html lang="en">
<head>
<meta charset="utf-8">
<title>KR Appraisals – Services</title>
<link rel="stylesheet" href="https://fonts.googleapis.com/css2?family=Montserrat:wght@500;600&family=Nunito+Sans:wght@400;600&display=swap">
<style>
:root{
  --orange:#f37122;
  --green:#9bcb3c;
  --blue:#0355a3;
  --nav-grey:#6f6f6f;
  --text-grey:#666;
  --panel:#f2f2f2;
  --dark:#333333;
  --footer-line:#8a8a8a;
  --footer-text:#a9a9a9;
  --white:#ffffff;
}
*{margin:0;padding:0;box-sizing:border-box}
html,body{width:1200px;height:1144px;overflow:hidden;background:var(--white)}
body{position:relative;font-family:"Nunito Sans",sans-serif;color:var(--text-grey)}
.heading-font{font-family:"Montserrat",sans-serif}

.site-header{position:absolute;left:0;top:0;width:1200px;height:100px;
  background:linear-gradient(90deg,#e4e5dc 0%,#eceee3 45%,#f4f5e6 100%)}
.brand{position:absolute;display:flex;align-items:center;gap:10px}
.brand-mark{width:16px;height:16px;background:currentColor}
.brand-name{font-family:"Montserrat",sans-serif;font-weight:500;letter-spacing:.5px}
.site-header .brand{left:161px;top:36px;color:#7c7c7c}
.site-header .brand-name{font-size:22px}

.main-nav{position:absolute;top:45px;left:611px;display:flex;gap:41px;
  font-family:"Montserrat",sans-serif;font-weight:600;font-size:11px;color:var(--nav-grey);letter-spacing:.1px}
.main-nav .active{color:var(--blue)}

.page-title{position:absolute;top:186px;left:0;width:1200px;text-align:center;
  font-family:"Montserrat",sans-serif;font-weight:600;font-size:37px;color:var(--orange);letter-spacing:-.5px}

.service-panel{position:absolute;left:562px;top:281px;width:477px;height:420px;background:var(--panel)}
.service-photo{position:absolute;left:161px;top:341px;width:439px;height:293px;
  background:linear-gradient(120deg,#3a3631 0%,#6d5a48 40%,#8a7b6c 60%,#3c4a5a 100%)}
.service-title{position:absolute;left:639px;top:393px;font-family:"Montserrat",sans-serif;font-weight:600;
  font-size:29px;line-height:37px;color:var(--green);letter-spacing:-.3px}
.service-text{position:absolute;left:639px;top:490px;width:370px;font-size:11px;line-height:18.8px;color:var(--text-grey)}

.site-footer{position:absolute;left:0;top:790px;width:1200px;height:354px}
.footer-shape{position:absolute;left:0;top:0}
.site-footer .brand{left:0;width:1200px;justify-content:center;top:62px;color:#8f8f8f}
.site-footer .brand-name{font-size:22px}
.footer-rule{position:absolute;left:161px;width:879px;height:1px;background:var(--footer-line)}
.footer-nav{position:absolute;top:159px;left:386px;display:flex;gap:40px;
  font-family:"Montserrat",sans-serif;font-weight:600;font-size:11px;color:#8d8d8d}
.footer-nav .active{color:var(--green)}
.footer-col{position:absolute;top:218px;font-size:11px;line-height:22.5px;color:var(--footer-text)}
.footer-col h3{font-family:"Montserrat",sans-serif;font-weight:600;font-size:14px;color:var(--orange);margin-bottom:10px;line-height:18px}
.footer-col .hl{color:var(--green)}
.footer-col .wh{color:#e8e8e8}
.contact-line{display:flex;gap:9px;align-items:flex-start;line-height:16.5px}
.contact-line.phone{margin-top:14px;font-size:11.5px;color:#f0f0f0;align-items:center}
.contact-line svg{flex:none;margin-top:1px}
.badge{position:absolute;border-radius:4px}
.badge-one{left:856px;top:212px;width:170px;height:34px;background:#5a5a5a}
.badge-two{left:854px;top:258px;width:170px;height:70px;background:#e9e9e9;border-radius:6px}
</style>
</head>
<body>

<header class="site-header">
  <div class="brand"><span class="brand-mark"></span><span class="brand-name">KR APPRAISALS</span></div>
  <nav class="main-nav">
    <span>HOME</span><span>ABOUT</span><span class="active">SERVICES</span><span>NEWS &amp; VIEWS</span><span>CONTACT</span>
  </nav>
</header>

<h1 class="page-title">OUR SERVICES</h1>

<section class="service">
  <div class="service-panel"></div>
  <div class="service-photo" role="img" aria-label="Photo of three colleagues at a wooden table reviewing a bar chart on a laptop"></div>
  <h2 class="service-title">BUSINESS PLAN<br>COACHING</h2>
  <p class="service-text">Young companies and entrepreneurs frequently ask for our advice on their business plans and strategies. With almost 2 decades of analyzing companies large and small, we are well positioned to advise companies based on experience and insight.</p>
</section>

<footer class="site-footer">
  <svg class="footer-shape" width="1200" height="354" viewBox="0 0 1200 354" aria-hidden="true">
    <polygon points="0,69 600,1 1200,69 1200,354 0,354" fill="var(--dark)"/>
  </svg>
  <div class="brand"><span class="brand-mark"></span><span class="brand-name">KR APPRAISALS</span></div>
  <div class="footer-rule" style="top:146px"></div>
  <nav class="footer-nav">
    <span class="active">HOME</span><span>ABOUT</span><span>SERVICES</span><span>NEWS &amp; VIEWS</span><span>CONTACT</span>
  </nav>
  <div class="footer-rule" style="top:191px"></div>

  <div class="footer-col" style="left:163px">
    <h3>CREDITS</h3>
    <div>© 2019 <span class="hl">KR Appraisals</span></div>
    <div>Logo by <span class="wh">Mara Lindqvist</span></div>
    <div>Website by <span class="hl">Northlane Web</span></div>
  </div>

  <div class="footer-col" style="left:390px">
    <h3>LEIDEN</h3>
    <div class="contact-line">
      <svg width="9" height="12" viewBox="0 0 9 12"><path d="M4.5 0A4.5 4.5 0 0 0 0 4.5C0 8 4.5 12 4.5 12S9 8 9 4.5A4.5 4.5 0 0 0 4.5 0Z" fill="var(--green)"/><circle cx="4.5" cy="4.5" r="1.7" fill="var(--dark)"/></svg>
      <div>Lindenlaan 48<br>2311 AB Leiden</div>
    </div>
    <div class="contact-line phone">
      <svg width="12" height="12" viewBox="0 0 24 24"><path d="M6.6 10.8a15 15 0 0 0 6.6 6.6l2.2-2.2c.3-.3.7-.4 1-.2 1.1.4 2.3.6 3.6.6.6 0 1 .4 1 1V20c0 .6-.4 1-1 1A17 17 0 0 1 3 4c0-.6.4-1 1-1h3.5c.6 0 1 .4 1 1 0 1.3.2 2.5.6 3.6.1.3 0 .7-.2 1Z" fill="var(--green)"/></svg>
      <span>070 555 0142</span>
    </div>
  </div>

  <div class="footer-col" style="left:617px">
    <h3>AMSTERDAM</h3>
    <div class="contact-line">
      <svg width="9" height="12" viewBox="0 0 9 12"><path d="M4.5 0A4.5 4.5 0 0 0 0 4.5C0 8 4.5 12 4.5 12S9 8 9 4.5A4.5 4.5 0 0 0 4.5 0Z" fill="var(--green)"/><circle cx="4.5" cy="4.5" r="1.7" fill="var(--dark)"/></svg>
      <div>Keizersplein 14<br>1017 XY Amsterdam</div>
    </div>
    <div class="contact-line phone">
      <svg width="12" height="12" viewBox="0 0 24 24"><path d="M6.6 10.8a15 15 0 0 0 6.6 6.6l2.2-2.2c.3-.3.7-.4 1-.2 1.1.4 2.3.6 3.6.6.6 0 1 .4 1 1V20c0 .6-.4 1-1 1A17 17 0 0 1 3 4c0-.6.4-1 1-1h3.5c.6 0 1 .4 1 1 0 1.3.2 2.5.6 3.6.1.3 0 .7-.2 1Z" fill="var(--green)"/></svg>
      <span>020 555 0187</span>
    </div>
  </div>

  <div class="badge badge-one" role="img" aria-label="Professional membership badge"></div>
  <div class="badge badge-two" role="img" aria-label="Accreditation badge"></div>
</footer>

</body>
</html>
```